Logo, Web and Mobile Designs for enterprise social media platform

All the details are in the attached document, please start reading the scope document first which explains what is this project about and the details about the needed deliverables, after that please read the UI_Requirements document which will detail what is expected regarding the coded web version since this is a coded contest, it is very important that you meet the UI requirements or suggest something else but we will need to agree first before working on the coded version

Good Luck

Target Market(s)

Enterprise Social Media

Industry/Entity Type

Media

Coding

Coded - Design and coding required

Number of Pages Required

5+ page

Font styles to use
Sans Serif

Requirements
Must have
• All the must haves are listed in the scope document so please check before you start

```html
<!DOCTYPE html>
<html lang="en">
<head>
<meta charset="utf-8">
<title>Teamora – Create New Business Opportunity, Step 3</title>
<link rel="stylesheet" href="https://fonts.googleapis.com/css2?family=Open+Sans:ital,wght@0,400;0,600;0,700;1,400&family=Roboto:wght@300;400;500&family=Roboto+Condensed:wght@400&display=swap">
<style>
:root{
  --page-bg:#f7f7f7;
  --header-bg:#fafafa;
  --line:#e2e2e2;
  --icon-grey:#7a7a7a;
  --brand-blue:#2a9fd6;
  --brand-orange:#f39c12;
  --card-head-bg:#f4f5f7;
  --label:#5a5a5a;
  --text-dark:#333333;
  --text-body:#555555;
  --save:#e68a00;
  --save-shadow:#b86d00;
  --footer:#1e8ab5;
  --white:#ffffff;
}
*{box-sizing:border-box;margin:0;padding:0}
html,body{width:1200px;height:3297px;overflow:hidden}
body{position:relative;background:var(--page-bg);font-family:'Open Sans',sans-serif;color:var(--text-body)}
.site-header{position:absolute;left:0;top:0;width:1200px;height:233px;background:linear-gradient(#ffffff,#f3f3f3);border-bottom:4px solid var(--line)}
.header-btn{position:absolute;top:0;height:229px;width:213px;display:flex;align-items:center;justify-content:center}
.header-btn.home{left:0;border-right:2px solid var(--line)}
.header-btn.menu{right:0;width:208px;border-left:2px solid var(--line)}
.brand{position:absolute;left:345px;top:60px;height:110px;display:flex;align-items:center;gap:22px}
.brand-dot{width:88px;height:88px;border-radius:50%;background:var(--brand-orange)}
.brand-name{font-family:'Roboto',sans-serif;font-weight:400;font-size:76px;color:var(--brand-blue);letter-spacing:1px}
.card{position:absolute;left:43px;top:311px;width:1112px;height:2520px;background:var(--white);border:2px solid #e6e6e6}
.card-head{height:143px;background:var(--card-head-bg);border-bottom:2px solid #dcdcdc;padding-left:40px;display:flex;align-items:center;font-family:'Roboto',sans-serif;font-size:37px;color:#4f5660;letter-spacing:.5px}
.field-label{position:absolute;left:68px;font-size:40px;color:var(--label)}
.field{position:absolute;left:68px;width:986px;background:var(--white);border:2px solid #e3e3e3;border-radius:4px;font-size:35px;color:#444;display:flex;align-items:center;padding-left:64px}
.field.select .chevron{position:absolute;right:0;top:0;width:106px;height:100%;border-left:2px solid #e3e3e3;display:flex;align-items:center;justify-content:center}
.avatar{position:absolute;border-radius:50%}
.avatar.group{width:200px;height:200px;left:70px}
.avatar.member{width:166px;height:166px;left:277px}
.group-title{position:absolute;left:323px;font-family:'Roboto',sans-serif;font-weight:300;font-size:45px;color:var(--brand-blue)}
.group-desc{position:absolute;left:323px;font-style:italic;font-size:31px;line-height:57px;color:var(--text-body)}
.member-name{position:absolute;left:493px;font-family:'Roboto',sans-serif;font-weight:300;font-size:47px;color:var(--text-dark)}
.save-btn{position:absolute;left:80px;top:2329px;width:358px;height:105px;background:var(--save);border-radius:4px;box-shadow:0 6px 0 var(--save-shadow);color:var(--white);font-weight:600;font-size:44px;display:flex;align-items:center;justify-content:center;letter-spacing:1px}
.site-footer{position:absolute;left:0;top:2928px;width:1200px;height:369px;background:var(--footer);color:var(--white);text-align:center}
.social{position:absolute;top:78px;left:0;width:100%;display:flex;justify-content:center;gap:30px;padding-left:10px}
.social span{width:60px;height:60px;border-radius:10px;background:var(--white)}
.footer-links{position:absolute;top:172px;left:0;width:100%;font-family:'Roboto Condensed',sans-serif;font-size:36px;letter-spacing:.3px}
.footer-links span.sep{margin:0 22px}
.copyright{position:absolute;top:254px;left:0;width:100%;font-family:'Roboto',sans-serif;font-size:34px}
</style>
</head>
<body>
<header class="site-header">
  <div class="header-btn home">
    <svg width="48" height="42" viewBox="0 0 24 21" aria-label="Home"><path d="M12 1 1 11h3v9h6v-6h4v6h6v-9h3z" fill="var(--icon-grey)"/></svg>
  </div>
  <div class="brand"><span class="brand-dot"></span><span class="brand-name">Teamora</span></div>
  <div class="header-btn menu">
    <svg width="46" height="40" viewBox="0 0 23 20" aria-label="Menu"><rect y="0" width="23" height="4" rx="1" fill="var(--icon-grey)"/><rect y="8" width="23" height="4" rx="1" fill="var(--icon-grey)"/><rect y="16" width="23" height="4" rx="1" fill="var(--icon-grey)"/></svg>
  </div>
</header>

<main class="card">
  <div class="card-head">CREATE NEW BUSINESS OPPORTUNITY - STEP 3</div>

  <div class="field-label" style="top:212px">Add Member : *</div>
  <div class="field" style="top:298px;height:113px"></div>

  <div class="field-label" style="top:446px">Choose Group : *</div>
  <div class="field select" style="top:533px;height:110px">Create Group
    <span class="chevron"><svg width="26" height="16" viewBox="0 0 13 8"><path d="M1 1l5.5 5.5L12 1" fill="none" stroke="#555" stroke-width="1.6"/></svg></span>
  </div>
  <div class="field" style="top:666px;height:110px">Enter the new Group name</div>

  <div class="avatar group" style="top:852px;background:radial-gradient(circle at 45% 40%,#b48d72,#3c4658 70%)" role="img" aria-label="Administrators group photo"></div>
  <div class="group-title" style="top:852px">Administrators</div>
  <div class="group-desc" style="top:922px">Lorem ipsum dolor sit amet,<br>consectetur adipiscing elit, sed do</div>

  <div class="avatar member" style="top:1094px;background:radial-gradient(circle at 50% 45%,#d9b59c,#8a6b52 75%)" role="img" aria-label="Member photo"></div>
  <div class="member-name" style="top:1150px">Lina Farouk</div>
  <div class="avatar member" style="top:1297px;background:radial-gradient(circle at 50% 40%,#e5c3a8,#2d3748 78%)" role="img" aria-label="Member photo"></div>
  <div class="member-name" style="top:1353px">Omar Nabil</div>
  <div class="avatar member" style="top:1500px;background:radial-gradient(circle at 50% 40%,#d8ab8a,#8fa6bb 78%)" role="img" aria-label="Member photo"></div>
  <div class="member-name" style="top:1556px">Karim Adel</div>

  <div class="avatar group" style="top:1753px;background:radial-gradient(circle at 50% 50%,#c7b9a2,#5f7c8e 75%)" role="img" aria-label="Buyers group photo"></div>
  <div class="group-title" style="top:1753px">Buyers</div>
  <div class="group-desc" style="top:1823px">Lorem ipsum dolor sit amet,<br>consectetur adipiscing elit, sed do</div>

  <div class="avatar group" style="top:2029px;background:radial-gradient(circle at 50% 45%,#e8e2da,#8d8479 78%)" role="img" aria-label="Sellers group photo"></div>
  <div class="group-title" style="top:2029px">Sellers</div>
  <div class="group-desc" style="top:2099px">Lorem ipsum dolor sit amet,<br>consectetur adipiscing elit, sed do</div>

  <div class="save-btn">SAVE</div>
</main>

<footer class="site-footer">
  <div class="social" aria-label="Social links"><span></span><span></span><span></span><span></span><span></span></div>
  <div class="footer-links">Home<span class="sep">/</span>Contact<span class="sep">/</span>Topics<span class="sep">/</span>Posts &amp; Comments<span class="sep">/</span>Videos Links</div>
  <div class="copyright">Copyright @ 2015 - 2015.Teamora. All Rights Reserved.</div>
</footer>
</body>
</html>
```